RM Tomás Ledesma (Business Card)

Hi designers, in this work, I'm looking for an sophisticated stylish, elegant and proffesional personal card. We have a laboratory of pathology automated, with equipments high quality.
In this web the designers, have created my business logo, the name is "RM Tomás Ledesma"
In our lab, we principal work is to prepare the biopsies for further diagnostic of diseases like cancer, tumors, etc.
I need that the first face, only having my complete logo (Rm Tomás Ledesma, Laboratorio de procesamiento Histologico)
The overleaf, could repeat the same logo, like water logo.
In this face, I need to say: My full data:

Técnico en Anatomía Patológica
Tomás Ledesma Urquiza M.P 48213
Av. Duarte Quirós 817 - 2do piso - Instituto Brandsen.
Córdoba, Argentina
(0351) 158246093
ledesma.tomas@correoviva.com.ar

with respect the colors of card, use your imagination, the original logo color is violet, I haven't chosen a color base for the card.

attached pictures are examples of cards I like your DESIGN.
Attached too, the original logo to my company.

the size of card are:
horizontal: 9cm
vertical: 5,5cm

any question that you have, not doubt to question me,
Hand to work!

Industry/Entity Type

Laboratory

Requirements
Must have
• designers sophisticated, not simples, like show the images attached

```html
<!DOCTYPE html>
<html lang="es">
<head>
<meta charset="utf-8">
<title>Tomás Ledesma – Tarjeta personal</title>
<link href="https://fonts.googleapis.com/css2?family=Arimo:wght@700&family=Ubuntu:wght@400;500&family=Roboto+Condensed:wght@400&display=swap" rel="stylesheet">
<style>
  :root {
    --backdrop: #2b2b2d;
    --violet: #7e3aa8;
    --violet-deep: #5f2a86;
    --violet-back-top: #7a3a9e;
    --violet-back-bottom: #5e2680;
    --paper: #f2f2f2;
    --arc-grey: #9a9a9a;
    --arc-grey-light: #c4c4c4;
    --ink-light: #ffffff;
    --ink-soft: #ece4f2;
    --logo-grey: #d9d9d9;
  }
  * { margin: 0; padding: 0; box-sizing: border-box; }
  html, body {
    width: 1200px; height: 900px; overflow: hidden;
    background: var(--backdrop);
  }
  .canvas { position: relative; width: 1200px; height: 900px; }

  .card {
    position: absolute; left: 370px; width: 456px; height: 279px;
    border-radius: 14px; overflow: hidden;
    box-shadow: 0 6px 18px rgba(0,0,0,.45);
  }

  /* Front */
  .card-front { top: 161px; background: var(--paper); }
  .card-front .shape { position: absolute; inset: 0; }
  .front-mark {
    position: absolute; left: 40px; top: 128px;
    display: flex; align-items: center; gap: 8px;
    font-family: "Ubuntu", sans-serif; font-weight: 500; font-size: 16px;
    color: var(--violet);
  }
  .front-mark .dot { width: 10px; height: 10px; background: var(--violet); }

  .info {
    position: absolute; right: 18px; text-align: right;
    color: var(--ink-light);
    font-family: "Ubuntu", sans-serif; font-size: 11.5px; line-height: 15px;
  }
  .holder-name {
    top: 57px; font-family: "Arimo", sans-serif; font-weight: 700; font-size: 16px; line-height: 20px;
  }
  .holder-reg { top: 78px; font-size: 13px; }
  .contact { top: 162px; right: 18px; }
  .contact li { list-style: none; display: flex; justify-content: flex-end; align-items: center; gap: 10px; }
  .contact svg { width: 10px; height: 10px; fill: var(--ink-light); }
  .credentials { top: 215px; }

  /* Back */
  .card-back {
    top: 471px;
    background: linear-gradient(180deg, var(--violet-back-top), var(--violet-back-bottom));
    color: var(--logo-grey); text-align: center;
  }
  .back-mark {
    position: absolute; left: 0; right: 0; top: 118px;
    display: flex; justify-content: center; align-items: center; gap: 10px;
    font-family: "Ubuntu", sans-serif; font-size: 17px; letter-spacing: 5px;
    color: var(--logo-grey);
  }
  .back-mark .ring { width: 12px; height: 12px; border: 1.5px solid var(--logo-grey); border-radius: 50%; }
  .mark-rule {
    position: absolute; left: 88px; width: 276px; top: 145px; height: 1px; background: var(--logo-grey);
  }
  .tagline {
    position: absolute; left: 0; right: 0; top: 150px;
    font-family: "Roboto Condensed", sans-serif; font-size: 20px; color: var(--ink-soft);
  }
  .divider {
    position: absolute; left: 20px; right: 20px; top: 207px; height: 1px;
    background: linear-gradient(90deg, transparent, rgba(255,255,255,.45), transparent);
  }
  .website {
    position: absolute; left: 0; right: 0; top: 232px;
    font-family: "Ubuntu", sans-serif; font-size: 13px; color: var(--ink-soft);
  }
</style>
</head>
<body>
<div class="canvas">

  <section class="card card-front">
    <svg class="shape" viewBox="0 0 456 279" preserveAspectRatio="none">
      <defs>
        <linearGradient id="frontViolet" x1="0" y1="0" x2="0" y2="1">
          <stop offset="0" stop-color="#8a3fb5"/>
          <stop offset="1" stop-color="#6a2c92"/>
        </linearGradient>
      </defs>
      <path d="M190 0 Q262 130 168 279" fill="none" stroke="var(--arc-grey)" stroke-width="7"/>
      <path d="M200 0 Q262 140 176 279" fill="none" stroke="var(--arc-grey-light)" stroke-width="3"/>
      <path d="M206 0 Q258 140 180 279 L456 279 L456 0 Z" fill="url(#frontViolet)"/>
    </svg>

    <div class="front-mark"><span class="dot"></span>Tomás Ledesma</div>

    <p class="info holder-name">Tomás Ledesma Urquiza</p>
    <p class="info holder-reg">M.P. 48213</p>

    <ul class="info contact">
      <li>(0351) 158246093
        <svg viewBox="0 0 10 10"><path d="M2 0h2l1 3-1.3 1a5 5 0 0 0 2.3 2.3L7 5l3 1v2a2 2 0 0 1-2 2A8 8 0 0 1 0 2a2 2 0 0 1 2-2z"/></svg>
      </li>
      <li>ledesma.tomas@correoviva.com.ar
        <svg viewBox="0 0 10 10"><path d="M0 2h10v7H0z M0 2l5 4 5-4" fill="none" stroke="#fff" stroke-width="1.2"/></svg>
      </li>
    </ul>

    <div class="info credentials">
      <p>Técnico en Anatomía Patológica</p>
      <p>Av. Duarte Quirós 817 - 2do piso</p>
      <p>Instituto Brandsen, Córdoba, Argentina</p>
    </div>
  </section>

  <section class="card card-back">
    <div class="back-mark"><span class="ring"></span>TOMÁS LEDESMA</div>
    <div class="mark-rule"></div>
    <p class="tagline">LABORATORIO DE PROCESAMIENTO HISTOLOGICO</p>
    <div class="divider"></div>
    <p class="website">www.Tomas-Ledesma.com</p>
  </section>

</div>
</body>
</html>
```